Accountability Project Graphics

I want to create 10 social media graphics (new Instagram size 4:5 (1080 x 1350 pixels) focusing on our Quilvo Accountability App, using any of the 3 pictures attached. Use the attached pics only, NO RANDOM STOCK PHOTOGRAPHY. For the color scheme, use the landing page colors/fonts (attached).
You can add any of the 3 photos attached but I mainly need BOLD text that includes these headlines and sub-headlines on them.
Please NOTE for all the headlines below, also add this sub-headline on each graphic:
Stay Consistent with RT in Your Pocket!
Here are the headlines:
• Stop Starting Over Every Monday
• You don't need more willpower. You need more support
• Built for women who are tired of doing this alone
• When Motivation Fades, RT Checks In
• The Support System You've Been Missing
• Support When Motivation Disappears
• What if RT Checked in Every Day?
• The Missing Piece Isn't Another Diet
• Eat the food you love. Stay accountable every day.
• One Bad Meal Doesn't Mean You Failed
women over 40 trying to lose weight

```html
<!DOCTYPE html>
<html lang="en">
<head>
<meta charset="UTF-8">
<title>Support When Motivation Disappears</title>
<link href="https://fonts.googleapis.com/css2?family=Playfair+Display:wght@700&family=Outfit:wght@400;500&family=Caveat:wght@500&display=swap" rel="stylesheet">
<style>
  :root {
    --paper: #f7ece9;
    --paper-deep: #f1dcd9;
    --ink: #231030;
    --plum: #2a1232;
    --pink: #e0437a;
    --pink-soft: #f3a6c0;
    --note: #f4eee6;
    --white: #ffffff;
    --rule: #e6c8cc;
  }
  * { margin: 0; padding: 0; box-sizing: border-box; }
  html, body { width: 960px; height: 1200px; overflow: hidden; background: var(--paper); }
  .poster {
    position: relative; width: 960px; height: 1200px; overflow: hidden;
    background: linear-gradient(160deg, #faf2ef 0%, var(--paper) 55%, var(--paper-deep) 100%);
    font-family: "Outfit", sans-serif; color: var(--ink);
  }
  .photo {
    position: absolute; left: 430px; top: 0; width: 530px; height: 1010px;
    background: linear-gradient(180deg, #f3c6d4 0%, #eab2c6 35%, #e9c9c6 65%, #eee2d4 100%);
    -webkit-mask-image: linear-gradient(90deg, transparent 0%, #000 24%, #000 100%);
    mask-image: linear-gradient(90deg, transparent 0%, #000 24%, #000 100%);
  }
  .headline { position: absolute; left: 47px; top: 122px; font-family: "Playfair Display", serif; font-weight: 700; }
  .headline .line { display: block; }
  .headline .dark { font-size: 100px; color: var(--ink); letter-spacing: -1px; line-height: 0.98; }
  .headline .accent { font-size: 82px; color: var(--pink); letter-spacing: -1px; line-height: 0.98; }
  .headline .dark + .accent { margin-top: 6px; }
  .heart-mark { position: absolute; left: 346px; top: 240px; }
  .swoosh { position: absolute; left: 40px; top: 508px; }
  .tagline { position: absolute; left: 49px; top: 542px; font-size: 22px; font-weight: 500; line-height: 29px; }
  .tagline .accent { color: var(--pink); }
  .features { position: absolute; left: 48px; top: 618px; list-style: none; }
  .feature { display: flex; align-items: center; height: 81px; position: relative; }
  .feature + .feature::before {
    content: ""; position: absolute; left: 80px; top: 0; width: 135px; height: 1px; background: var(--rule);
  }
  .feature .badge {
    width: 62px; height: 62px; border-radius: 50%; background: var(--pink);
    display: flex; align-items: center; justify-content: center; flex: none;
  }
  .feature span { margin-left: 18px; font-size: 16px; line-height: 20px; }
  .checks { position: absolute; left: 49px; top: 862px; list-style: none; }
  .check { display: flex; align-items: center; height: 55px; }
  .check span { margin-left: 13px; font-size: 14px; line-height: 17px; font-weight: 500; }
  .band { position: absolute; left: 0; top: 955px; }
  .note {
    position: absolute; left: 320px; top: 806px; width: 338px; height: 244px;
    background: var(--note); transform: rotate(-2deg);
    box-shadow: 0 6px 18px rgba(35,16,48,0.25);
    clip-path: polygon(0 3%, 20% 0, 45% 2%, 70% 0, 100% 2%, 99% 40%, 100% 75%, 98% 100%, 60% 98%, 30% 100%, 1% 98%, 0 60%);
  }
  .note p {
    position: absolute; left: 48px; top: 70px; font-family: "Caveat", cursive; font-weight: 500;
    font-size: 38px; line-height: 46px; color: var(--ink); transform: rotate(-4deg);
  }
  .note p em { font-style: normal; color: var(--pink); }
  .note svg { position: absolute; left: 160px; top: 176px; }
  .tape { position: absolute; left: 404px; top: 782px; width: 140px; height: 50px; background: rgba(230,120,160,0.7); transform: rotate(-1deg); }
  .brand {
    position: absolute; left: 47px; top: 1063px; width: 90px; height: 90px; border-radius: 50%;
    background: var(--pink); box-shadow: 0 0 0 3px var(--plum), 0 0 0 5px var(--pink);
    display: flex; align-items: center; justify-content: center;
    font-family: "Outfit", sans-serif; font-weight: 500; font-size: 38px; color: var(--white);
  }
  .cheer { position: absolute; left: 165px; top: 1064px; color: var(--white); }
  .cheer .ask { font-size: 23px; font-weight: 400; }
  .cheer .reply { font-family: "Caveat", cursive; font-size: 38px; color: var(--pink); transform: rotate(-3deg); display: block; margin-top: 2px; }
  .cheer svg { display: block; margin-top: 2px; }
  .divider { position: absolute; left: 409px; top: 1078px; width: 1px; height: 86px; background: var(--pink-soft); opacity: 0.6; }
  .promise { position: absolute; left: 440px; top: 1072px; font-size: 16px; line-height: 23px; color: var(--white); }
</style>
</head>
<body>
<main class="poster">
  <div class="photo" role="img" aria-label="Photo of two women sharing a joyful hug, one in a pink top and one in a pastel ruffled top"></div>

  <h1 class="headline">
    <span class="line dark">Support</span>
    <span class="line dark">When</span>
    <span class="line accent">Motivation</span>
    <span class="line accent">Disappears</span>
  </h1>
  <svg class="heart-mark" width="80" height="76" viewBox="0 0 80 76" aria-hidden="true">
    <path d="M40 68 C20 52 6 40 8 24 C10 10 28 6 38 22 C46 6 68 6 72 22 C76 40 56 54 40 68 Z" fill="none" stroke="var(--pink)" stroke-width="3" stroke-linecap="round"/>
  </svg>
  <svg class="swoosh" width="340" height="20" viewBox="0 0 340 20" aria-hidden="true">
    <path d="M4 14 C90 4 220 2 334 7" stroke="var(--pink)" stroke-width="4" fill="none" stroke-linecap="round"/>
  </svg>

  <p class="tagline">Real support. Real results.<br><span class="accent">Stay Consistent with RT in Your Pocket!</span></p>

  <ul class="features">
    <li class="feature">
      <div class="badge"><svg width="30" height="30" viewBox="0 0 24 24" fill="none" stroke="#fff" stroke-width="2" stroke-linecap="round" stroke-linejoin="round"><path d="M5 3h3l2 5-2 1.5a11 11 0 0 0 6 6L15.5 14l5 2v3a2 2 0 0 1-2 2A16 16 0 0 1 3 5a2 2 0 0 1 2-2z"/><path d="M15 3a6 6 0 0 1 6 6M15 7a2 2 0 0 1 2 2"/></svg></div>
      <span>Weekly<br>calls from RT</span>
    </li>
    <li class="feature">
      <div class="badge"><svg width="32" height="30" viewBox="0 0 24 24" fill="none" stroke="#fff" stroke-width="1.8" stroke-linecap="round"><path d="M3 17h18M5 17a7 7 0 0 1 14 0M12 8V6M10 6h4M3 20h18"/></svg></div>
      <span>Meal help<br>and recipes</span>
    </li>
    <li class="feature">
      <div class="badge"><svg width="32" height="30" viewBox="0 0 24 24" fill="none" stroke="#fff" stroke-width="1.8" stroke-linejoin="round"><path d="M3 5h12v8H8l-3 3v-3H3z"/><path d="M15 9h6v8h-2v3l-3-3h-5v-4"/><circle cx="6.5" cy="9" r=".6" fill="#fff"/><circle cx="9" cy="9" r=".6" fill="#fff"/><circle cx="11.5" cy="9" r=".6" fill="#fff"/></svg></div>
      <span>Text support<br>and motivation</span>
    </li>
  </ul>

  <ul class="checks">
    <li class="check">
      <svg width="36" height="36" viewBox="0 0 36 36" aria-hidden="true"><circle cx="18" cy="18" r="16" fill="none" stroke="var(--pink)" stroke-width="2"/><path d="M10 18l6 6 12-13" fill="none" stroke="var(--pink)" stroke-width="2.5" stroke-linecap="round" stroke-linejoin="round"/></svg>
      <span>Daily accountability<br>from RT</span>
    </li>
    <li class="check">
      <svg width="36" height="36" viewBox="0 0 36 36" aria-hidden="true"><circle cx="18" cy="18" r="16" fill="none" stroke="var(--pink)" stroke-width="2"/><path d="M10 18l6 6 12-13" fill="none" stroke="var(--pink)" stroke-width="2.5" stroke-linecap="round" stroke-linejoin="round"/></svg>
      <span>Delicious meals<br>and recipes</span>
    </li>
  </ul>

  <svg class="band" width="960" height="245" viewBox="0 0 960 245" aria-hidden="true">
    <path d="M0 70 C220 30 520 20 960 8 L960 245 L0 245 Z" fill="var(--plum)"/>
  </svg>

  <div class="note">
    <p>You don't have<br>to do this <em>alone.</em></p>
    <svg width="56" height="52" viewBox="0 0 56 52" aria-hidden="true"><path d="M28 46 C14 34 4 26 6 15 C8 6 22 4 27 16 C32 4 48 5 50 15 C52 27 40 36 28 46 Z" fill="none" stroke="var(--pink)" stroke-width="2.5" stroke-linecap="round"/></svg>
  </div>
  <div class="tape"></div>

  <div class="brand">RT</div>
  <div class="cheer">
    <span class="ask">You good, sis?</span>
    <span class="reply">You've got this!</span>
    <svg width="200" height="12" viewBox="0 0 200 12" aria-hidden="true"><path d="M4 9 C70 3 140 2 196 4" stroke="var(--pink)" stroke-width="3" fill="none" stroke-linecap="round"/></svg>
  </div>
  <div class="divider"></div>
  <p class="promise">RT is here to<br>keep you encouraged,<br>consistent, and<br>moving forward.</p>
</main>
</body>
</html>
```